Quillfern Vaults - Direct Mailer / Flyer

We are excited to announce the launch of our new company, Quillfern Vaults, a premier cohosting facility and data center dedicated to Cryptocurrency Miners. Our website, https://quillfernvaults.example, provides detailed information about our offerings and showcases the innovative design schemes for the entire project.

Quillfern Vaults stands out in the industry by offering both GPU Hosting and ASIC Hosting services in our state-of-the-art facility, equipped with an impressive 17 Megawatts of available power. What sets us apart is our unique billing system based on actual metered power usage. We charge $0.08 for ASIC miners and $0.09 for GPU miners, ensuring cost-effectiveness and transparency for our clients.

Our commitment to excellence is evident in our use of cutting-edge technology, top-notch facilities, and strategic partnerships. These elements come together to deliver exceptional solutions tailored for real-world applications in the cryptocurrency space.

As part of our promotional efforts, we are developing a direct mailer/flyer to introduce Quillfern Vaults to a wider audience. This promotional material will also serve as a handout at events, to potential customers, and more. We welcome creative ideas and suggestions to maximize the versatility of this design and reach diverse target audiences effectively.

For a comprehensive overview of our services and to explore our design concepts, please visit https://quillfernvaults.example. Quillfern Vaults is poised to revolutionize the mining industry, and we look forward to partnering with you for success in the digital currency era.

```html
<!DOCTYPE html>
<html lang="en">
<head>
<meta charset="utf-8">
<title>Quillfern Vaults – Cohosting Flyer</title>
<link href="https://fonts.googleapis.com/css2?family=Roboto:wght@400;500;700;900&display=swap" rel="stylesheet">
<style>
  :root {
    --page: #f3f4f7;
    --frame: #dcdde2;
    --ink-dark: #3a3836;
    --ink-body: #5d5d63;
    --headline-red: #ee0a24;
    --white: #ffffff;
    --gpu-blue: #3a57ff;
    --asic-green: #078a2a;
    --hero-deep: #050507;
    --hero-mid: #2a2b30;
  }
  * { box-sizing: border-box; margin: 0; padding: 0; }
  html, body { width: 927px; height: 1200px; overflow: hidden; }
  body {
    position: relative;
    background: radial-gradient(circle at 20% 60%, #ffffff 0%, var(--page) 55%, #e9ebf0 100%);
    font-family: "Roboto", Arial, sans-serif;
  }
  .frame {
    position: absolute; left: 21px; top: 15px; width: 885px; height: 1170px;
    border: 1px solid var(--frame);
  }
  .brand {
    position: absolute; left: 23px; top: 33px; height: 89px;
    display: flex; align-items: center; gap: 26px;
  }
  .brand-mark {
    width: 97px; height: 89px; background: var(--ink-dark); border-radius: 3px;
  }
  .brand-name {
    font-weight: 900; font-size: 72px; letter-spacing: 5px; color: var(--ink-dark);
    text-transform: uppercase; line-height: 1; white-space: nowrap;
  }
  .tagline {
    position: absolute; left: 0; width: 927px; top: 148px; text-align: center;
    color: var(--headline-red); font-weight: 900; font-size: 41px; letter-spacing: 0.5px;
  }
  .hero {
    position: absolute; left: 28px; top: 213px; width: 871px; height: 461px;
    background:
      radial-gradient(ellipse at 50% 40%, rgba(120,120,130,0.55) 0%, rgba(40,40,46,0.4) 35%, transparent 65%),
      linear-gradient(90deg, var(--hero-mid) 0%, var(--hero-deep) 25%, var(--hero-deep) 75%, var(--hero-mid) 100%);
  }
  .hero-copy {
    position: absolute; left: 28px; top: 213px; width: 871px; height: 461px;
    text-align: center; color: var(--white);
  }
  .hero-title {
    font-weight: 900; font-size: 55px; line-height: 63px; margin-top: 120px;
    text-shadow: 0 2px 4px rgba(0,0,0,0.6);
  }
  .hero-text {
    width: 540px; margin: 21px auto 0; font-weight: 500; font-size: 13.2px; line-height: 28px;
  }
  .about { position: absolute; left: 64px; top: 720px; width: 378px; }
  .section-title {
    font-weight: 900; font-size: 30px; color: var(--ink-dark); line-height: 36px;
    text-shadow: 1px 1px 0 #aaa;
  }
  .about p {
    font-size: 11.2px; line-height: 25px; color: var(--ink-body); margin-top: 14px;
  }
  .about p + p { margin-top: 25px; }
  .about .section-title.values { margin-top: 24px; }
  .plan {
    position: absolute; left: 487px; width: 396px; height: 220px;
    border-radius: 12px; color: var(--white);
  }
  .plan-gpu { top: 725px; background: var(--gpu-blue); }
  .plan-asic { top: 964px; background: var(--asic-green); }
  .plan-icon {
    position: absolute; left: 20px; top: 23px; width: 63px; height: 61px;
    background: var(--white); border-radius: 6px;
    display: flex; align-items: center; justify-content: center;
  }
  .plan-body { position: absolute; left: 109px; top: 22px; width: 280px; }
  .plan-title { font-weight: 700; font-size: 21.5px; line-height: 28px; }
  .plan-desc { font-size: 11.6px; line-height: 23.4px; margin-top: 5px; }
  .plan-list { list-style: none; margin-top: 5px; }
  .plan-list li {
    position: relative; padding-left: 18px; font-size: 11.2px; line-height: 24.7px;
    white-space: nowrap;
  }
  .plan-list li::before {
    content: ""; position: absolute; left: 1px; top: 8px; width: 5px; height: 5px;
    border: 1.5px solid var(--white); border-radius: 50%;
  }
</style>
</head>
<body>
  <div class="frame"></div>

  <header class="brand">
    <div class="brand-mark"></div>
    <div class="brand-name">Quillfern Vaults</div>
  </header>

  <h1 class="tagline">TRANSFORM MINING WITH COHOSTING</h1>

  <div class="hero" role="img" aria-label="Photograph of a dark data center aisle lined with server racks"></div>
  <section class="hero-copy">
    <h2 class="hero-title">YOUR MINING SUCCESS<br>STORY BEGINS HERE</h2>
    <p class="hero-text">What sets us apart is our unique billing system based on actual metered power usage. We charge $0.08 for ASIC miners and $0.09 for GPU miners, ensuring cost-effectiveness and transparency for our clients.</p>
  </section>

  <section class="about">
    <h3 class="section-title">WHO WE ARE</h3>
    <p>At Quillfern Vaults, our mission is to empower cryptocurrency miners by providing transparent, efficient, and reliable cohosting solutions.</p>
    <p>We strive to optimize mining operations through innovative technology, fair pricing models, and exceptional customer support, fostering growth and sustainability in the cryptocurrency landscape.</p>
    <h3 class="section-title values">OUR VALUES</h3>
    <p>At Quillfern Vaults, we uphold integrity, transparency, and innovation as our core values.</p>
    <p>We are committed to fostering trust, accountability, and sustainability in all our interactions. By prioritizing these values with our continuous improvement, we strive to be the trusted partner of choice for cryptocurrency miners.</p>
  </section>

  <article class="plan plan-gpu">
    <div class="plan-icon">
      <svg width="44" height="32" viewBox="0 0 44 32" fill="none" stroke="#3a57ff" stroke-width="1.6">
        <path d="M2 3h3v26"/>
        <rect x="5" y="5" width="37" height="19" rx="2"/>
        <circle cx="17" cy="14.5" r="6"/><circle cx="17" cy="14.5" r="2"/>
        <circle cx="32" cy="14.5" r="6"/><circle cx="32" cy="14.5" r="2"/>
        <path d="M9 24v4h22v-4"/>
      </svg>
    </div>
    <div class="plan-body">
      <h4 class="plan-title">GPU HOSTING ($0.09)</h4>
      <p class="plan-desc">Benefit from GPU hosting at an affordable rate of $0.09 per kilowatt-hour, ensuring cost-effective operations for your mining needs on any algorithm.</p>
      <ul class="plan-list">
        <li>One Time Setup Fee of $50 Per GPU Rig</li>
        <li>All-In $0.09 Per Kilowatt-Hour, No Additional Fees</li>
        <li>Remotely Monitor &amp; Access Your Equipment 24/7</li>
      </ul>
    </div>
  </article>

  <article class="plan plan-asic">
    <div class="plan-icon">
      <svg width="44" height="44" viewBox="0 0 44 44" fill="none" stroke="#078a2a" stroke-width="1.6">
        <rect x="11" y="11" width="22" height="22" rx="1"/>
        <rect x="16" y="16" width="12" height="12"/>
        <path d="M16 11V4M22 11V4M28 11V4M16 33v7M22 33v7M28 33v7M11 16H4M11 22H4M11 28H4M33 16h7M33 22h7M33 28h7"/>
      </svg>
    </div>
    <div class="plan-body">
      <h4 class="plan-title">ASIC HOSTING ($0.08)</h4>
      <p class="plan-desc">Access ASIC hosting at a competitive rate of $0.08 per kilowatt-hour, ensuring efficient and cost-effective operations for your large scale mining</p>
      <ul class="plan-list">
        <li>One Time Setup Fee of $50 Per GPU Rig</li>
        <li>All-In $0.09 Per Kilowatt-Hour, No Additional Fees</li>
        <li>Remotely Monitor &amp; Access Your Equipment 24/7</li>
      </ul>
    </div>
  </article>
</body>
</html>
```